Brekwell Automotive needs a catchy banner design

We need a design for a banner to be displayed on the fence in the outfield of a baseball stadium to show off our company and have people interested in what we do. We need something catchy that's going to attract people to look over at our banner.
We are a
Complete Automotive Service Company
Tires - Service - Repair - Diesel
We are in a Town called Fuquay-Varina
(555)314-2609 we would like the phone number to be a descent size so when you are in the stands you can read it.
I have attached what we came up with but like I said we need it to pop more and make the viewer that's looking at it want to look us up.
The Banner size is 24ft long and 10ft tall

```html
<!DOCTYPE html>
<html lang="en">
<head>
<meta charset="utf-8">
<title>Brekwell Automotive – Outfield Banner</title>
<link href="https://fonts.googleapis.com/css2?family=Anton&family=Open+Sans:wght@400;600&display=swap" rel="stylesheet">
<style>
  :root{
    --blue:#1b62e6;
    --blue-deep:#0c4cc4;
    --blue-bright:#2a7cf7;
    --blue-light:#3d8bf5;
    --gray:#7c7c7c;
    --gray-text:#7a7a7a;
    --ink:#111;
    --white:#fff;
    --car-light:#dbe8fd;
    --car-mid:#a9c6f8;
  }
  *{margin:0;padding:0;box-sizing:border-box}
  html,body{width:1200px;height:500px;overflow:hidden;background:var(--white)}
  .banner{position:relative;width:1200px;height:500px;overflow:hidden;background:var(--white)}
  .backdrop{position:absolute;inset:0;width:1200px;height:500px}

  .car-visual{position:absolute;left:485px;top:133px;width:700px;height:240px;
    background:linear-gradient(135deg,var(--car-light) 0%,var(--car-mid) 100%)}

  .brand{position:absolute;left:41px;top:46px;display:flex;align-items:center;gap:10px;
    font-family:"Anton",sans-serif;font-size:26px;color:var(--blue);letter-spacing:.5px;line-height:1}
  .brand-mark{width:16px;height:16px;background:var(--blue)}

  .headline{position:absolute;left:40px;top:150px;font-family:"Anton",sans-serif;font-weight:400;
    font-size:35px;line-height:52px;color:var(--blue);letter-spacing:0;text-transform:uppercase}
  .town{position:absolute;left:40px;top:264px;font-family:"Open Sans",sans-serif;font-weight:600;
    font-size:17px;color:var(--gray-text);letter-spacing:.3px}
  .phone{position:absolute;left:40px;top:306px;display:flex;align-items:center;gap:13px;
    font-family:"Open Sans",sans-serif;font-size:27px;color:var(--blue-bright);letter-spacing:-.2px}
  .phone svg{width:31px;height:31px}

  .services{position:absolute;left:40px;top:389px;display:flex;gap:29px;list-style:none}
  .service{width:49px;display:flex;flex-direction:column;align-items:center;gap:7px}
  .service svg{width:49px;height:35px}
  .service-label{font-family:"Anton",sans-serif;font-size:11px;color:var(--ink);letter-spacing:.2px;white-space:nowrap}
</style>
</head>
<body>
<div class="banner">
  <svg class="backdrop" viewBox="0 0 1200 500" aria-hidden="true">
    <polygon points="527,0 557,0 720,160 690,160" fill="var(--blue-light)"/>
    <polygon points="566,0 795,0 925,130 700,140" fill="var(--blue-deep)"/>
    <polygon points="1200,42 1200,190 1080,310 1000,250" fill="var(--gray)"/>
    <polygon points="359,500 566,500 740,326 533,326" fill="var(--gray)"/>
    <polygon points="566,500 950,500 1110,340 726,340" fill="var(--blue-bright)"/>
    <polygon points="950,500 1200,250 1200,500" fill="var(--blue-deep)"/>
    <g stroke="var(--white)" stroke-width="1.2">
      <line x1="1020" y1="500" x2="1200" y2="320"/>
      <line x1="1045" y1="500" x2="1200" y2="345"/>
      <line x1="1070" y1="500" x2="1200" y2="370"/>
      <line x1="1095" y1="500" x2="1200" y2="395"/>
    </g>
  </svg>

  <div class="car-visual" role="img" aria-label="Photo of a white sports car with a blue tint, front three-quarter view, with its reflection on the floor"></div>

  <div class="brand"><span class="brand-mark"></span>Brekwell Automotive</div>

  <h1 class="headline">Complete Automotive<br>Service</h1>
  <p class="town">FUQUAY-VARINA</p>

  <p class="phone">
    <svg viewBox="0 0 32 32" aria-hidden="true" fill="none" stroke="var(--blue-bright)" stroke-width="2" stroke-linejoin="round" stroke-linecap="round">
      <path d="M7 3 L12 3 L14 10 L10.5 12.5 C12 16.5 15.5 20 19.5 21.5 L22 18 L29 20 L29 25 C29 27 27 29 25 29 C13 28 4 19 3 7 C3 5 5 3 7 3 Z"/>
      <path d="M19 3 C24 4 28 8 29 13"/>
      <path d="M18 8 C21 8.7 23.3 11 24 14"/>
    </svg>
    (555)314-2609
  </p>

  <ul class="services">
    <li class="service">
      <svg viewBox="0 0 49 35" aria-hidden="true"><polygon points="2,9 24.5,1 47,9 47,26 24.5,34 2,26" fill="var(--white)" stroke="var(--blue)" stroke-width="2"/><circle cx="24.5" cy="17.5" r="7" fill="none" stroke="var(--blue)" stroke-width="1.5"/><circle cx="24.5" cy="17.5" r="2.5" fill="var(--blue)"/></svg>
      <span class="service-label">TIRES</span>
    </li>
    <li class="service">
      <svg viewBox="0 0 49 35" aria-hidden="true"><polygon points="2,9 24.5,1 47,9 47,26 24.5,34 2,26" fill="var(--white)" stroke="var(--blue)" stroke-width="2"/><rect x="19" y="12" width="11" height="11" fill="none" stroke="var(--blue)" stroke-width="1.5"/></svg>
      <span class="service-label">SERVICE</span>
    </li>
    <li class="service">
      <svg viewBox="0 0 49 35" aria-hidden="true"><polygon points="2,9 24.5,1 47,9 47,26 24.5,34 2,26" fill="var(--white)" stroke="var(--blue)" stroke-width="2"/><circle cx="24.5" cy="17.5" r="6" fill="none" stroke="var(--blue)" stroke-width="2.5" stroke-dasharray="3 2"/></svg>
      <span class="service-label">REPAIR</span>
    </li>
    <li class="service">
      <svg viewBox="0 0 49 35" aria-hidden="true"><polygon points="2,9 24.5,1 47,9 47,26 24.5,34 2,26" fill="var(--white)" stroke="var(--blue)" stroke-width="2"/><rect x="20" y="11" width="9" height="13" rx="1" fill="none" stroke="var(--blue)" stroke-width="1.5"/><line x1="29" y1="14" x2="32" y2="12" stroke="var(--blue)" stroke-width="1.5"/></svg>
      <span class="service-label">DIESEL</span>
    </li>
  </ul>
</div>
</body>
</html>
```